Harborline Lending and Capital. We provide MOSTLY residential home mortgages in Florida AND commercial loans for investment properties throughout the United states.
I would love to emulate so of the lender sites that are available on the internet but I would like to have the site as popular as possible for SEO purposes. Clients can already click the link to take them to the mortgage application where they can complete that and upload documents. If you could polish that up for me that would be great. I can also provide you with great detail on loan programs that are currently being offered. WE OFFER ALL MORTGAGE LENDING PRODUCTS. I would also like to add something in reference to the rate but I don't think it's legal to actually state or promise a rate for mortgage since they vary based on loan type, client and other criteria...

On the Harborline real estate site I would like to add a link or some way for clients to be able to put in credit card information to render services ...

Please let me know what you need from me

Thank you !!

Current link to site to improve and code

https://harborlinelendingandcapital.example/

Industry/Entity Type

Residential and commmercial lending

Coding

Coded - Design and coding required

Number of Pages Required

2 page

Requirements
Must have
• Love to integrate Mortgage interest rates even if general
Nice to have
• Link to fill out mortgage application via Quorvel LPX software

```html
<!DOCTYPE html>
<html lang="en">
<head>
<meta charset="utf-8">
<title>Harborline Lending and Capital of Florida</title>
<link rel="stylesheet" href="https://fonts.googleapis.com/css2?family=Montserrat:wght@700;800&family=Figtree:wght@300;400;500;600&display=swap">
<style>
:root{
  --green-dark:#1e3b1f;
  --green-deep:#244a22;
  --green-lime:#8dc63f;
  --ink:#1b1b1b;
  --muted:#666;
  --line:#c9c9c9;
  --soft-bg:#f4f4f4;
  --footer:#1c1c1c;
  --white:#fff;
}
*{box-sizing:border-box;margin:0;padding:0}
html,body{width:1200px;height:3104px;overflow:hidden}
body{position:relative;font-family:"Figtree",sans-serif;color:var(--ink);background:var(--white)}
.abs{position:absolute}
h1,h2,h3{font-family:"Montserrat",sans-serif;font-weight:800}

/* header */
.site-header{left:0;top:0;width:1200px;height:88px;background:var(--white)}
.brand{left:145px;top:14px;display:flex;align-items:center;gap:10px}
.brand-mark{width:54px;height:54px;border-radius:50%;background:var(--green-dark)}
.brand-name{font-size:7px;font-weight:600;color:var(--green-dark);line-height:1.6;text-transform:uppercase;letter-spacing:.3px}
.brand-name span{display:block;color:#8a8a8a;font-weight:400;letter-spacing:1.6px;font-size:5px}
.nav a{position:absolute;top:37px;font-size:15px;color:var(--ink);text-decoration:none;text-transform:uppercase}
.nav .active{left:507px;top:31px;width:71px;height:28px;line-height:28px;text-align:center;border-radius:14px;color:#fff;background:linear-gradient(90deg,var(--green-deep),var(--green-lime))}

/* hero */
.hero{left:0;top:88px;width:1200px;height:594px}
.hero-photo{position:absolute;inset:0;background:linear-gradient(100deg,#4a4d4f 0%,#6b6e6f 45%,#8d9294 70%,#5d6466 100%)}
.hero-kicker{left:143px;top:120px;font-size:15px;color:#fff}
.hero-title{left:141px;top:152px;font-size:39px;line-height:60px;color:#fff;letter-spacing:.5px}
.hero-sub{left:143px;top:348px;font-size:18px;color:#fff}
.hero-cta{left:142px;top:406px;width:545px;height:49px;border:2px solid var(--green-lime);border-radius:25px;background:var(--green-dark);color:#fff;font-weight:700;font-size:16px;display:flex;align-items:center;padding-left:25px;gap:10px}

.dot-icon{width:14px;height:14px;border-radius:50%;background:#fff;display:inline-flex;align-items:center;justify-content:center}

/* about */
.about-accent{left:143px;top:810px;width:291px;height:301px;background:var(--green-lime)}
.about-photo{left:170px;top:745px;width:406px;height:342px;background:linear-gradient(160deg,#a9bfa5 0%,#4f5f48 45%,#7a5a3a 65%,#6aa53e 100%)}
.section-title{text-align:center;font-size:38px;color:var(--ink)}
.rule{height:4px;width:80px;background:var(--green-lime)}
.about-text{left:648px;top:870px;width:414px;text-align:center;font-size:14px;line-height:24px;color:var(--muted);font-weight:300}
.pill-btn{height:44px;border-radius:22px;background:linear-gradient(90deg,var(--green-dark),var(--green-lime));color:#fff;font-size:14px;font-weight:600;display:flex;align-items:center;justify-content:center;gap:8px}

/* properties */
.prop{top:1302px;width:289px;height:296px}
.prop-label{position:absolute;bottom:24px;left:0;right:0;text-align:center;color:#fff;font-size:17px;font-weight:500}
.prop.featured{box-shadow:0 12px 24px rgba(0,0,0,.35)}
.slider-btn{top:1431px;width:36px;height:36px;border-radius:50%;background:#fff;display:flex;align-items:center;justify-content:center}

/* loans */
.loan{width:295px;height:181px;border:1px solid #9a9a9a;text-align:center;background:#fff}
.loan-num{margin-top:14px;font-family:"Montserrat",sans-serif;font-weight:700;font-size:32px;color:var(--green-lime)}
.loan-rule{margin:6px 17px 0;height:1px;background:var(--green-lime)}
.loan-title{margin-top:20px;font-size:17px;color:var(--ink)}
.loan-text{margin-top:8px;font-size:14px;line-height:23px;color:#555;font-weight:300}
.loan.highlight{border:none;background:linear-gradient(110deg,var(--green-dark),var(--green-lime))}
.loan.highlight .loan-num,.loan.highlight .loan-title,.loan.highlight .loan-text{color:#fff}
.loan.highlight .loan-rule{background:#b9de86}

/* contact */
.contact-band{left:0;top:2260px;width:1200px;height:616px;background:var(--soft-bg)}
.contact-dark{left:104px;top:2330px;width:416px;height:359px;background:var(--green-dark)}
.contact-kicker{right:128px;top:94px;width:260px;text-align:right;color:var(--green-lime);font-size:17px}
.contact-head{right:128px;top:126px;width:270px;text-align:right;color:#fff;font-size:37px;line-height:45px}
.contact-frame{left:694px;top:2349px;width:341px;height:323px;border:5px solid var(--green-lime)}
.form-card{left:432px;top:2378px;width:584px;height:405px;background:#fff;box-shadow:0 6px 22px rgba(0,0,0,.08)}
.form-title{left:50px;top:32px;font-size:32px;color:var(--ink)}
.field{width:214px}
.field label{display:block;font-size:15px;color:#333}
.field .ph{display:block;margin-top:10px;padding:0 2px 9px;font-size:11px;color:#999;border-bottom:1px solid var(--line)}
.send-btn{left:468px;top:304px;width:60px;height:60px;border-radius:50%;background:linear-gradient(135deg,var(--green-dark),var(--green-lime));display:flex;align-items:center;justify-content:center}

/* footer */
.site-footer{left:0;top:2876px;width:1200px;height:228px;background:var(--footer)}
.footer-nav{left:0;top:61px;width:1200px;text-align:center;color:#fff;font-size:17px;font-weight:500;word-spacing:2px}
.footer-nav span{margin:0 22px}
.footer-rule{left:143px;top:105px;width:913px;height:1px;background:#666}
.copyright{left:0;top:121px;width:1200px;text-align:center;color:#fff;font-size:14px}
.social{top:159px;width:32px;height:32px;border-radius:50%;border:1.5px solid #fff;display:flex;align-items:center;justify-content:center}
.social i{width:8px;height:8px;border-radius:50%;background:#fff}
.social.on{background:var(--green-lime);border-color:var(--green-lime)}
</style>
</head>
<body>

<header class="site-header abs">
  <div class="brand abs">
    <div class="brand-mark"></div>
    <div class="brand-name">Harborline Lending and Capital of Florida<span>Business and Commercial Division</span></div>
  </div>
  <nav class="nav">
    <a class="active">Home</a>
    <a style="left:620px">About</a>
    <a style="left:725px">Properties</a>
    <a style="left:867px">Careers</a>
    <a style="left:988px">Contact</a>
  </nav>
</header>

<section class="hero abs">
  <div class="hero-photo" role="img" aria-label="Business professionals walking through a bright modern office corridor"></div>
  <p class="hero-kicker abs">Welcome To Harborline Lending and Capital of Florida</p>
  <h1 class="hero-title abs">RESIDENTIAL HOME LOANS<br>IN FLORIDA &amp; COMMERCIAL<br>LENDING IN AMERICA</h1>
  <p class="hero-sub abs">Your Best Resource For Hassle-free, Low Cost Mortgage Origination</p>
  <div class="hero-cta abs">FILL OUT MORTGAGE APPLICATION TO BEGIN LENDING PR
    <span class="dot-icon"><svg width="8" height="8" viewBox="0 0 8 8"><path d="M2 1l3 3-3 3" stroke="#1e3b1f" stroke-width="1.6" fill="none"/></svg></span>
  </div>
</section>

<section>
  <div class="about-accent abs"></div>
  <div class="about-photo abs" role="img" aria-label="Modern two-storey house with timber cladding under a large tree"></div>
  <h2 class="section-title abs" style="left:648px;top:778px;width:414px">ABOUT US</h2>
  <div class="rule abs" style="left:815px;top:839px"></div>
  <p class="about-text abs">Harborline Lending Originates Residential Home loans in Florida and Commercial and business financing in all 50 States. We have over 25 years of experience in ALL types of real estate and commercial lending.</p>
  <div class="pill-btn abs" style="left:778px;top:1001px;width:152px">LEARN MORE
    <span class="dot-icon"><svg width="8" height="8" viewBox="0 0 8 8"><path d="M2 1l3 3-3 3" stroke="#1e3b1f" stroke-width="1.6" fill="none"/></svg></span>
  </div>
</section>

<section>
  <h2 class="section-title abs" style="left:0;top:1196px;width:1200px">AVAILABLE PROPERTIES</h2>
  <div class="rule abs" style="left:534px;top:1262px;width:132px"></div>
  <div class="prop abs" style="left:0;background:linear-gradient(180deg,#cfcac3,#8a8580 60%,#3b3a3a)" role="img" aria-label="Townhouse facade with balcony"><span class="prop-label">12 Sunset Street</span></div>
  <div class="prop featured abs" style="left:304px;background:linear-gradient(180deg,#2e4650,#1e2c32 55%,#6b5330)" role="img" aria-label="Dark modern house at dusk with timber screen"><span class="prop-label">34 Union Avenue
    <svg style="margin-left:36px;vertical-align:middle" width="22" height="14" viewBox="0 0 22 14"><path d="M1 7h19M14 1l6 6-6 6" stroke="#fff" stroke-width="2" fill="none"/></svg></span></div>
  <div class="prop abs" style="left:607px;background:linear-gradient(180deg,#9fb6c8,#c9b8a0 50%,#3f6f78)" role="img" aria-label="Courtyard house with pool and perforated screen"><span class="prop-label">56 Washington Street</span></div>
  <div class="prop abs" style="left:911px;background:linear-gradient(90deg,#545c63,#3b4147 40%,#8a4a3a 70%,#2a2f35)" role="img" aria-label="Modern facade with red timber and dark panels"><span class="prop-label">78 Oak Boulevard</span></div>
  <div class="slider-btn abs" style="left:16px"><svg width="10" height="12" viewBox="0 0 10 12"><path d="M7 1L2 6l5 5" stroke="#222" stroke-width="2" fill="none"/></svg></div>
  <div class="slider-btn abs" style="left:1148px"><svg width="10" height="12" viewBox="0 0 10 12"><path d="M3 1l5 5-5 5" stroke="#222" stroke-width="2" fill="none"/></svg></div>
</section>

<section>
  <h2 class="section-title abs" style="left:0;top:1692px;width:1212px">LOAN PROGRAMS</h2>
  <div class="rule abs" style="left:549px;top:1758px;width:68px"></div>
  <div class="loan abs" style="left:145px;top:1806px"><div class="loan-num">01</div><div class="loan-rule"></div><div class="loan-title">Duis aute irure dolor</div><div class="loan-text">Lorem ipsum dolor sit amet, consectetur<br>adipiscing elit, sed do eiusmod</div></div>
  <div class="loan abs" style="left:452px;top:1806px"><div class="loan-num">02</div><div class="loan-rule"></div><div class="loan-title">Duis aute irure dolor</div><div class="loan-text">Lorem ipsum dolor sit amet, consectetur<br>adipiscing elit, sed do eiusmod</div></div>
  <div class="loan abs" style="left:759px;top:1806px"><div class="loan-num">03</div><div class="loan-rule"></div><div class="loan-title">Duis aute irure dolor</div><div class="loan-text">Lorem ipsum dolor sit amet, consectetur<br>adipiscing elit, sed do eiusmod</div></div>
  <div class="loan abs" style="left:145px;top:2000px"><div class="loan-num">04</div><div class="loan-rule"></div><div class="loan-title">Duis aute irure dolor</div><div class="loan-text">Lorem ipsum dolor sit amet, consectetur<br>adipiscing elit, sed do eiusmod</div></div>
  <div class="loan highlight abs" style="left:452px;top:2000px"><div class="loan-num">05</div><div class="loan-rule"></div><div class="loan-title">Duis aute irure dolor</div><div class="loan-text">Lorem ipsum dolor sit amet, consectetur<br>adipiscing elit, sed do eiusmod</div></div>
  <div class="loan abs" style="left:759px;top:2000px"><div class="loan-num">06</div><div class="loan-rule"></div><div class="loan-title">Duis aute irure dolor</div><div class="loan-text">Lorem ipsum dolor sit amet, consectetur<br>adipiscing elit, sed do eiusmod</div></div>
</section>

<section>
  <div class="contact-band abs"></div>
  <svg class="abs" style="left:72px;top:2594px" width="140" height="140" viewBox="0 0 140 140">
    <defs><pattern id="dots" width="13" height="13" patternUnits="userSpaceOnUse"><circle cx="2" cy="2" r="1.5" fill="#555"/></pattern></defs>
    <rect x="0" y="0" width="16" height="140" fill="url(#dots)"/>
    <rect x="0" y="104" width="140" height="36" fill="url(#dots)"/>
  </svg>
  <div class="contact-dark abs">
    <p class="contact-kicker abs">CONTACT US</p>
    <h2 class="contact-head abs">LET’S DO<br>GOOD<br>TOGETHER!</h2>
  </div>
  <div class="contact-frame abs"></div>
  <form class="form-card abs">
    <h2 class="form-title abs">SEND US A MESSAGE</h2>
    <div class="field abs" style="left:53px;top:92px"><label>Your Name</label><span class="ph">John Smith</span></div>
    <div class="field abs" style="left:311px;top:92px"><label>Full Name</label><span class="ph">John Smith</span></div>
    <div class="field abs" style="left:53px;top:178px"><label>Email Address</label><span class="ph">info@harborline.example</span></div>
    <div class="field abs" style="left:311px;top:178px"><label>Phone</label><span class="ph">01155-214-873-602</span></div>
    <div class="field abs" style="left:53px;top:257px;width:420px"><label>Message</label><span class="ph" style="padding-bottom:34px">Lorem ipsum dolor sit amet, .....</span></div>
    <div class="send-btn abs"><svg width="22" height="22" viewBox="0 0 22 22"><path d="M2 11L20 3l-6 17-3-7z" fill="#fff"/></svg></div>
  </form>
</section>

<footer class="site-footer abs">
  <p class="footer-nav abs">HOME<span>/</span>ABOUT US<span>/</span>PROPERTIES<span>/</span>CAREERS<span>/</span>CONTACT US</p>
  <div class="footer-rule abs"></div>
  <p class="copyright abs">Copyright © Harborline Lending and Capital of Florida - All Rights Reserved</p>
  <div class="social abs" style="left:544px"><i></i></div>
  <div class="social on abs" style="left:584px"><i></i></div>
  <div class="social abs" style="left:623px"><i></i></div>
</footer>

</body>
</html>
```